Design a compelling Tarnwove Business Card that will drive people to my site

I want a business card that I can give to people—less to tell them who I am and more to direct them to my website. My website is a portal for Pelmor Aquatics Officials and a place for people who want to become Pelmor Aquatics Officials.
I am uploading my official company logo as well as a business card mockup that I did on my own. Please feel free to completely stray from this design.
I've included a screen recording of the homepage of my website as well.
Target Market(s)
Pelmor Aquatics Officials and people who desire to become one
Contact Information for Business Card
website url
Look and feel
Each slider illustrates characteristics of the customer's brand and the style your logo design should communicate.

```html
<!DOCTYPE html>
<html lang="en">
<head>
<meta charset="utf-8">
<title>Tarnwove Business Card</title>
<link rel="stylesheet" href="https://fonts.googleapis.com/css2?family=Poppins:wght@400;500;600;700&display=swap">
<style>
  :root {
    --page: #e8e9ee;
    --card: #3a52a6;
    --card-deep: #32489a;
    --accent: #93a8e3;
    --ink: #ffffff;
    --rule: #7e93d3;
  }
  * { box-sizing: border-box; margin: 0; padding: 0; }
  html, body { width: 1186px; height: 1200px; overflow: hidden; }
  body {
    background: var(--page);
    font-family: "Poppins", sans-serif;
    color: var(--ink);
    position: relative;
  }
  .card {
    position: absolute;
    left: 113px;
    width: 960px;
    height: 540px;
    background: var(--card);
    overflow: hidden;
    box-shadow: 0 10px 24px rgba(20, 30, 70, 0.25);
  }
  .card--front { top: 40px; }
  .card--back { top: 620px; }

  .brand {
    position: absolute;
    font-weight: 600;
    letter-spacing: -1px;
    line-height: 1;
    color: var(--ink);
    white-space: nowrap;
  }
  .card--front .brand { left: 70px; top: 268px; font-size: 66px; }
  .brand-dot {
    position: absolute;
    left: 210px; top: 196px;
    width: 46px; height: 46px;
    border-radius: 50%;
    background: var(--accent);
  }
  .divider {
    position: absolute;
    left: 480px; top: 172px;
    width: 2px; height: 196px;
    background: var(--rule);
  }
  .contact { position: absolute; left: 508px; top: 176px; }
  .contact__name { font-size: 34px; font-weight: 700; color: var(--accent); line-height: 1.15; white-space: nowrap; }
  .contact__role { font-size: 26px; font-weight: 400; line-height: 1.3; margin-bottom: 26px; }
  .contact__line {
    display: flex; align-items: center; gap: 8px;
    font-size: 27px; font-weight: 400; line-height: 1.32;
    white-space: nowrap;
  }
  .contact__line svg { width: 20px; height: 20px; flex: none; }

  .pattern-field {
    position: absolute; inset: 0;
    background: linear-gradient(135deg, var(--card) 0%, var(--card-deep) 100%);
  }
  .card--back .brand { left: 326px; top: 228px; font-size: 64px; }
  .tagline {
    position: absolute; left: 320px; top: 362px;
    font-size: 29px; font-weight: 400; letter-spacing: 0.3px;
    white-space: nowrap;
  }
  .tagline-dot {
    position: absolute; left: 238px; top: 364px;
    width: 36px; height: 36px; border-radius: 50%;
    background: var(--accent);
  }
</style>
</head>
<body>
  <section class="card card--front" aria-label="Business card front">
    <span class="brand-dot"></span>
    <div class="brand">tarnwove</div>
    <div class="divider"></div>
    <div class="contact">
      <div class="contact__name">Martin Vellano</div>
      <div class="contact__role">CEO &amp; Founder</div>
      <div class="contact__line">
        <svg viewBox="0 0 20 20" aria-hidden="true"><path fill="#fff" d="M3 7c0-2 3-3 7-3s7 1 7 3v2h-4V7.5C12 7 8 7 7 7.5V9H3zM5 10h10l1 6H4z"/></svg>
        (555) 014-2273
      </div>
      <div class="contact__line">
        <svg viewBox="0 0 20 20" aria-hidden="true"><path fill="#fff" d="M2 8l8-5 8 5v9H2z"/><path fill="none" stroke="#3a52a6" stroke-width="1.5" d="M2 8l8 5 8-5"/></svg>
        martin@tarnwove.com
      </div>
      <div class="contact__line">
        <svg viewBox="0 0 20 20" aria-hidden="true"><circle cx="10" cy="10" r="8" fill="#fff"/><path fill="#3a52a6" d="M6 6c2 0 3 1 3 3s-2 2-2 4l-2-1c-1-2 0-4 1-6zm7 2c1 1 2 2 1 4l-2 2-1-3z"/></svg>
        www.tarnwove.com
      </div>
    </div>
  </section>

  <section class="card card--back" aria-label="Business card back">
    <div class="pattern-field" role="img" aria-label="Embossed repeating brand-mark pattern in tone-on-tone blue"></div>
    <div class="brand">tarnwove</div>
    <span class="tagline-dot"></span>
    <div class="tagline">The Poolside Steward’s Hub</div>
  </section>
</body>
</html>
```